Software as a Service to manage Home Care Management

We need a web site designed for Home Care Management Software as a Service product, that facilitates Home Care organizations to manage and schedule carers to visit client homes. We want a modern look and feel using our existing logo.

Target Market(s)

Home Care Management organizations. Product is similar to: https://carelarkly.io/

Coding

Coded - Design and coding required

Number of Pages Required

3 page

```html
<!DOCTYPE html>
<html lang="en">
<head>
<meta charset="utf-8">
<title>Tendwise – Home Care Management</title>
<link href="https://fonts.googleapis.com/css2?family=Cinzel:wght@400;500;600&family=Roboto:wght@400;500;700&display=swap" rel="stylesheet">
<style>
:root{
  --pink:#f5337a;
  --pink-deep:#e8286e;
  --ink:#1e1e1e;
  --text:#555;
  --light:#f0f0f1;
  --dark:#2b2b2d;
  --darker:#222224;
  --white:#fff;
}
*{box-sizing:border-box;margin:0;padding:0}
html,body{width:1200px;height:3759px;overflow:hidden}
body{font-family:'Roboto',sans-serif;color:var(--ink);background:var(--white);position:relative}
.abs{position:absolute}
.serif{font-family:'Cinzel',serif}
.btn{position:absolute;display:flex;align-items:center;justify-content:center;font-weight:700;font-size:15px;text-transform:uppercase;border-radius:2px;letter-spacing:.2px}
.btn-pink{background:var(--pink);color:var(--white)}
.btn-white{background:var(--white);color:var(--pink)}
.btn-dark{background:var(--darker);color:var(--white)}

/* header */
.topline{top:0;left:0;width:1200px;height:6px;background:var(--pink)}
.header{top:6px;left:0;width:1200px;height:91px;background:var(--white)}
.brand{position:absolute;display:flex;align-items:center;gap:8px;font-family:'Cinzel',serif;font-weight:600;color:var(--ink)}
.brand .dot{width:16px;height:16px;border-radius:50%;background:var(--pink)}
.nav{position:absolute;top:36px;left:420px;display:flex;gap:26px;font-size:15px;font-weight:500}
.nav .active{color:var(--pink)}
.header-btn{top:24px;left:937px;width:151px;height:40px;font-size:15px;text-transform:none;font-weight:500;border-radius:3px}

/* hero */
.hero{top:97px;left:0;width:1200px;height:660px}
.hero-photo{position:absolute;inset:0;background:linear-gradient(90deg,#e9e9eb 0%,#d6d6d8 35%,#b2504e 62%,#c6a78b 85%,#b79a7e 100%)}
.hero-title{top:180px;left:110px;font-size:58px;font-weight:500;color:var(--ink);letter-spacing:1px}
.hero-title span{color:var(--pink)}
.hero-copy{top:260px;left:112px;width:470px;font-size:16px;line-height:27px;color:#222}
.hero-btn{top:343px;left:112px;width:234px;height:49px;font-size:16px;gap:8px}
.dots{top:588px;left:566px;display:flex;gap:5px}
.dots i{width:11px;height:11px;border-radius:50%;background:var(--white);display:block}
.dots i.on{background:transparent;border:2px solid var(--white)}

/* intro */
.intro{top:757px;left:0;width:1200px;height:541px;background:var(--pink)}
.intro h2{position:absolute;top:78px;left:565px;font-size:40px;line-height:44px;font-weight:500;color:var(--white);letter-spacing:1px}
.ticks{position:absolute;top:195px;left:565px;list-style:none;color:var(--white);font-size:14px}
.ticks li{display:flex;align-items:center;gap:17px;height:32px}
.ticks svg{flex:none}
.intro .btn-white{top:414px;left:566px;width:124px;height:42px;font-size:14px}
.intro .btn-dark{top:414px;left:707px;width:170px;height:42px;font-size:14px}

/* section heading */
.sec-title{position:absolute;left:0;width:1200px;text-align:center;font-family:'Cinzel',serif;font-size:40px;font-weight:500;letter-spacing:1px}
.sec-title span{color:var(--pink)}

/* audiences */
.audiences{top:1298px;left:0;width:1200px;height:612px;background:linear-gradient(135deg,#f4f4f5,#e9e9ea 50%,#f4f4f5)}
.card{position:absolute;top:194px;width:312px;height:326px;background:var(--white);box-shadow:0 2px 8px rgba(0,0,0,.08);text-align:center}
.card .icon{width:104px;height:104px;margin:34px auto 0;border-radius:50%;background:var(--pink);display:flex;align-items:center;justify-content:center}
.card h3{margin-top:28px;font-size:18px;font-weight:500}
.card p{margin:18px 22px 0;font-size:14px;line-height:24px;color:var(--text)}

/* numbers */
.numbers{top:1910px;left:0;width:1200px;height:746px;background:var(--white)}
.cell{position:absolute;width:325px;height:216px}
.photo{background:linear-gradient(135deg,#d9d7d6,#a7a4a3)}
.stat{text-align:center}
.stat b{display:block;margin-top:24px;font-size:36px;color:var(--pink);font-weight:700}
.stat p{margin:14px 28px 0;font-size:14px;line-height:23px;color:var(--text)}
.stat .btn{position:relative;margin:18px auto 0;width:124px;height:40px;font-size:15px}

/* partners */
.partners{top:2656px;left:0;width:1200px;height:364px;background:linear-gradient(135deg,#f4f4f5,#e8e8e9 50%,#f4f4f5)}
.partner{position:absolute;top:189px;width:168px;height:88px;background:var(--white);display:flex;align-items:center;justify-content:center}
.partner i{display:block;width:52px;height:52px;border-radius:50%;background:#e3e3e6}
.arrow{position:absolute;top:218px;width:30px;height:30px;border-radius:50%;background:var(--white);display:flex;align-items:center;justify-content:center;box-shadow:0 1px 4px rgba(0,0,0,.2)}

/* cta */
.cta{top:3020px;left:0;width:1200px;height:272px;background:var(--pink);color:var(--white);text-align:center}
.cta h2{margin-top:52px;font-family:'Cinzel',serif;font-size:40px;font-weight:500;letter-spacing:1px}
.cta p{margin:10px auto 0;width:760px;font-size:15px;line-height:24px}
.cta .btn{left:503px;top:170px;width:194px;height:48px;gap:8px}

/* footer */
.footer{top:3292px;left:0;width:1200px;height:416px;background:var(--dark);color:var(--white)}
.footer h4{position:absolute;top:90px;font-size:18px;font-weight:500}
.field{position:absolute;background:var(--white);color:#555;font-size:13px;padding:12px 18px}
.links{position:absolute;top:150px;list-style:none;font-size:15px}
.links li{height:33px;display:flex;align-items:flex-start;gap:12px}
.links li::before{content:"»";color:var(--pink);font-size:14px}
.footer .btn{top:322px;left:111px;width:134px;height:46px;border-radius:1px}
.bottom{top:3708px;left:0;width:1200px;height:51px;background:var(--darker);color:var(--white);font-size:15px}
.socials{position:absolute;top:14px;left:996px;display:flex;gap:6px}
.socials i{width:25px;height:25px;border-radius:50%;border:1.5px solid var(--white);display:block}
</style>
</head>
<body>

<div class="abs topline"></div>
<header class="abs header">
  <div class="brand" style="top:24px;left:110px;font-size:24px"><span class="dot"></span>Tendwise</div>
  <nav class="nav">
    <span class="active">Home</span><span>Product</span><span>Pricing</span><span>Blog</span><span>Contact us</span><span>Log In</span><span>En ⌄</span>
  </nav>
  <div class="btn btn-pink header-btn">Book a free demo</div>
</header>

<section class="abs hero">
  <div class="hero-photo" role="img" aria-label="Photo of a carer warmly hugging an elderly woman at home"></div>
  <svg class="abs" style="left:0;top:560px" width="1200" height="100" viewBox="0 0 1200 100" preserveAspectRatio="none">
    <path d="M0 0 C300 110 800 110 1200 0 L1200 100 L0 100Z" fill="#f5337a"/>
  </svg>
  <h1 class="abs hero-title serif">Tendwise <span>Care</span></h1>
  <p class="abs hero-copy">Lorem ipsum dolor sit amet, consectetur adipiscing elit, sed do eiusmod tempor incididunt ut labore</p>
  <div class="btn btn-pink hero-btn">See how it works
    <svg width="15" height="15" viewBox="0 0 16 16"><circle cx="8" cy="8" r="8" fill="#fff"/><path d="M6 4l4 4-4 4" stroke="#f5337a" stroke-width="2" fill="none"/></svg>
  </div>
  <div class="abs dots"><i></i><i></i><i class="on"></i><i></i><i></i></div>
</section>

<section class="abs intro">
  <svg class="abs" style="left:110px;top:50px" width="370" height="370" viewBox="0 0 370 370">
    <circle cx="185" cy="185" r="182" fill="none" stroke="rgba(255,255,255,.35)"/>
    <circle cx="185" cy="185" r="155" fill="rgba(255,255,255,.18)"/>
    <circle cx="185" cy="185" r="128" fill="rgba(255,255,255,.28)"/>
    <circle cx="185" cy="185" r="100" fill="rgba(255,255,255,.4)"/>
  </svg>
  <svg class="abs" style="left:188px;top:56px" width="214" height="428" viewBox="0 0 214 428">
    <rect x="2" y="2" width="210" height="424" rx="30" fill="#fff" stroke="#111" stroke-width="4"/>
    <rect x="10" y="10" width="194" height="408" rx="24" fill="#fff" stroke="#222" stroke-width="2"/>
    <path d="M68 10 h78 v8 a10 10 0 0 1 -10 10 h-58 a10 10 0 0 1 -10 -10Z" fill="#111"/>
  </svg>
  <div class="brand" style="top:262px;left:222px;font-size:22px"><span class="dot" style="width:12px;height:12px"></span>Tendwise</div>
  <h2 class="serif">Optimised Home Care<br>Software</h2>
  <ul class="ticks">
    <li><svg width="14" height="14" viewBox="0 0 14 14"><circle cx="7" cy="7" r="7" fill="#fff"/><path d="M4 7l2 2 4-4" stroke="#f5337a" stroke-width="2" fill="none"/></svg>Lorem ipsum dolor sit amet, consectetur adipiscing elit, sed do eiusmod</li>
    <li><svg width="14" height="14" viewBox="0 0 14 14"><circle cx="7" cy="7" r="7" fill="#fff"/><path d="M4 7l2 2 4-4" stroke="#f5337a" stroke-width="2" fill="none"/></svg>Tempor incididunt ut labore et dolore magna aliqua.</li>
    <li><svg width="14" height="14" viewBox="0 0 14 14"><circle cx="7" cy="7" r="7" fill="#fff"/><path d="M4 7l2 2 4-4" stroke="#f5337a" stroke-width="2" fill="none"/></svg>Ut enim ad minim veniam, quis nostrud exercitation ullamco laboris nisi</li>
    <li><svg width="14" height="14" viewBox="0 0 14 14"><circle cx="7" cy="7" r="7" fill="#fff"/><path d="M4 7l2 2 4-4" stroke="#f5337a" stroke-width="2" fill="none"/></svg>Ut aliquip ex ea commodo consequat. Duis aute irure dolor</li>
    <li><svg width="14" height="14" viewBox="0 0 14 14"><circle cx="7" cy="7" r="7" fill="#fff"/><path d="M4 7l2 2 4-4" stroke="#f5337a" stroke-width="2" fill="none"/></svg>In reprehenderit in voluptate velit esse cillum dolore eu fugiat pariatur.</li>
    <li><svg width="14" height="14" viewBox="0 0 14 14"><circle cx="7" cy="7" r="7" fill="#fff"/><path d="M4 7l2 2 4-4" stroke="#f5337a" stroke-width="2" fill="none"/></svg>Sed ut perspiciatis unde omnis iste natus error sit voluptatem accusantium</li>
  </ul>
  <div class="btn btn-white">Read more</div>
  <div class="btn btn-dark">Book a free demo</div>
</section>

<section class="abs audiences">
  <h2 class="sec-title" style="top:92px">We have made <span>Tendwise...</span></h2>
  <div class="card" style="left:110px">
    <div class="icon"><svg width="54" height="54" viewBox="0 0 54 54" fill="none" stroke="#fff" stroke-width="2"><circle cx="27" cy="18" r="7"/><circle cx="13" cy="24" r="5"/><circle cx="41" cy="24" r="5"/><path d="M15 46v-6a12 12 0 0 1 24 0v6M4 46v-4a9 9 0 0 1 11-8M50 46v-4a9 9 0 0 0-11-8"/></svg></div>
    <h3>For Managers</h3>
    <p>Sed ut perspiciatis unde omnis iste natus errordoloremque laudantium, totam rem aperiam, eaque ipsa quae beatae vitae dicta sunt explicabo.</p>
  </div>
  <div class="card" style="left:443px">
    <div class="icon"><svg width="54" height="54" viewBox="0 0 54 54" fill="none" stroke="#fff" stroke-width="2"><circle cx="17" cy="10" r="5"/><path d="M17 16v16M11 22h12M17 32l-5 14M17 32l5 14"/><circle cx="36" cy="38" r="9"/><circle cx="38" cy="18" r="4"/><path d="M36 23v10h10"/></svg></div>
    <h3>For Carers</h3>
    <p>Sed ut perspiciatis unde omnis iste natus errordoloremque laudantium, totam rem aperiam, eaque ipsa quae beatae vitae dicta sunt explicabo.</p>
  </div>
  <div class="card" style="left:777px">
    <div class="icon"><svg width="54" height="54" viewBox="0 0 54 54" fill="none" stroke="#fff" stroke-width="2"><path d="M27 14s-6-4-6-8a3 3 0 0 1 6-1 3 3 0 0 1 6 1c0 4-6 8-6 8z"/><circle cx="17" cy="26" r="6"/><circle cx="37" cy="26" r="6"/><path d="M6 48v-4a11 11 0 0 1 22 0v4M26 48v-4a11 11 0 0 1 22 0v4"/></svg></div>
    <h3>For Clients and Families</h3>
    <p>Sed ut perspiciatis unde omnis iste natus errordoloremque laudantium, totam rem aperiam, eaque ipsa quae beatae vitae dicta sunt explicabo.</p>
  </div>
</section>

<section class="abs numbers">
  <h2 class="sec-title" style="top:110px">Success in <span>numbers</span></h2>
  <div class="cell photo" style="top:210px;left:111px" role="img" aria-label="Photo of a nurse helping an elderly woman in a wheelchair"></div>
  <div class="cell stat" style="top:210px;left:436px"><b>96%</b><p>Lorem ipsum dolor sit amet, consectetur adipiscing elit, sed do eiusmod</p><div class="btn btn-pink">Read more</div></div>
  <div class="cell photo" style="top:210px;left:762px;background:linear-gradient(135deg,#e8dfcf,#9d9586)" role="img" aria-label="Photo of a carer and an elderly man sharing tea in a living room"></div>
  <div class="cell stat" style="top:426px;left:111px"><b>13M</b><p>Lorem ipsum dolor sit amet, consectetur adipiscing elit, sed do eiusmod</p><div class="btn btn-pink">Read more</div></div>
  <div class="cell photo" style="top:426px;left:436px;background:linear-gradient(135deg,#6e8fc3,#b7a6c4 60%,#8a5a34)" role="img" aria-label="Photo of a nurse talking with a smiling elderly woman holding a book"></div>
  <div class="cell stat" style="top:426px;left:762px"><b>17K</b><p>Lorem ipsum dolor sit amet, consectetur adipiscing elit, sed do eiusmod</p><div class="btn btn-pink">Read more</div></div>
</section>

<section class="abs partners">
  <h2 class="sec-title" style="top:112px">Working in <span>association with</span></h2>
  <div class="arrow" style="left:43px"><svg width="10" height="12" viewBox="0 0 10 12"><path d="M8 0L0 6l8 6Z" fill="#222"/></svg></div>
  <div class="partner" style="left:117px"><i></i></div>
  <div class="partner" style="left:316px"><i></i></div>
  <div class="partner" style="left:515px"><i></i></div>
  <div class="partner" style="left:714px"><i></i></div>
  <div class="partner" style="left:912px"><i></i></div>
  <div class="arrow" style="left:1125px"><svg width="10" height="12" viewBox="0 0 10 12"><path d="M2 0l8 6-8 6Z" fill="#222"/></svg></div>
</section>

<section class="abs cta">
  <h2>Ready to get started?</h2>
  <p>Sed ut perspiciatis unde omnis iste natus error sit voluptatem accusantium doloremque laudantium,aperiam, eaque ipsa quae ab illo inventore veritatis et vitae dicta sunt explicabo.</p>
  <div class="btn btn-dark">Book a free demo
    <svg width="15" height="15" viewBox="0 0 16 16"><circle cx="8" cy="8" r="8" fill="#fff"/><path d="M6 4l4 4-4 4" stroke="#222" stroke-width="2" fill="none"/></svg>
  </div>
</section>

<footer class="abs footer">
  <h4 style="left:111px">GET IN TOUCH</h4>
  <div class="field" style="top:130px;left:111px;width:270px;height:38px">First Name</div>
  <div class="field" style="top:130px;left:391px;width:270px;height:38px">Last Name</div>
  <div class="field" style="top:179px;left:111px;width:270px;height:38px">Email</div>
  <div class="field" style="top:179px;left:391px;width:270px;height:38px">Phone number</div>
  <div class="field" style="top:228px;left:111px;width:550px;height:74px">Message</div>
  <div class="btn btn-pink">Submit</div>
  <h4 style="left:740px">QUICK LINKS</h4>
  <ul class="links" style="left:740px"><li>Product</li><li>Pricing</li><li>Blog</li><li>FAQ</li><li>Contact us</li></ul>
  <h4 style="left:928px">APP</h4>
  <ul class="links" style="left:928px"><li>Managers</li><li>Carers</li><li>Customers &amp; Family</li></ul>
</footer>
<div class="abs bottom">
  <div class="abs" style="top:16px;left:111px">© 2020 Tendwise &nbsp;|&nbsp; Terms and Conditions &nbsp;|&nbsp; Privacy</div>
  <div class="socials"><i></i><i></i><i></i></div>
  <div class="abs" style="top:18px;left:1143px;font-size:11px">C37</div>
</div>

</body>
</html>
```